4D Cradle Glimpse Luxury Ultrasound Billboard

Design a HIGH-END, MODERN billboard for my private prenatal ultrasound studio, 4D Cradle Glimpse, located in Elmway, Florida.
This billboard will be viewed by drivers traveling at highway speeds, so it must be extremely clean, simple, and readable within 6 seconds.
About My Business
4D Cradle Glimpse is a private prenatal ultrasound studio specializing in:
Highest technology 4D/HD Ultrasounds
Early Gender Determination
Pregnancy Confirmation
I have been serving families for nearly 10 years and is known for creating a memorable experience, not just an ultrasound appointment.
Design Style
I DO NOT want:
Flowers
Leaves
Swirls
Glitter
Hearts everywhere
Busy backgrounds
Generic maternity stock graphics
I DO want:
Modern
Luxury
Upscale
Clean
Professional
Eye-catching
Premium medical spa feel
Colors
Use colors from my logo:
LOGO Green ( or a deep green)
Black
White
Soft Gold accents
Images:
Incorporate my professional headshot in a clean, modern way, logo, and the ultrasound images
Text
Keep wording minimal.
Primary Headline ( OPEN TO IDEAS) :
EXAMPLES ( WOULD RATHER SOMETHING MORE CATCHY)
" ADVANCED IMAGING. UNFORGETTABLE MOMENTS"
"MEET YOUR BABY BEFORE BIRTH"
Under headline:
4D Ultrasound • Early Gender • Pregnancy Confirmation
Business Name:
4D Cradle Glimpse
Private Prenatal Ultrasound Studio
Phone Number:
850-471-5923
Important
This billboard must be readable in 5–6 seconds from a moving vehicle.
Less text is better.
The phone number and business name must be visible from a distance.
The design should feel like a premium brand that immediately tells expecting parents:
“This is where I go to see my baby.”
Files Provided
Official logo
Headshot
Ultrasound images
Don’t make this look like a medical office billboard.
Make it look like a luxury baby experience billboard. That’s what separates 4D Cradle Glimpse from hospitals, OB offices, and all the new studios popping up around you. The emotional connection is what gets moms to book. ❤️
Billboard Size - 10.6” x 36”

```html
<!DOCTYPE html>
<html lang="en">
<head>
<meta charset="UTF-8">
<title>4D Cradle Glimpse Billboard</title>
<link rel="stylesheet" href="https://fonts.googleapis.com/css2?family=Montserrat:wght@400;500&family=Playfair+Display:wght@500&family=Great+Vibes&family=Poppins:wght@500;600&display=swap">
<style>
  :root {
    --deep-green: #2c3a30;
    --night: #1b211d;
    --cream: #f7f3ee;
    --gold: #c8963e;
    --gold-light: #ecc46c;
    --gold-dark: #a8722c;
    --ink: #1a1a1a;
    --white: #ffffff;
    --proof-pink: #f0157a;
    --guide: #e84bd8;
  }
  * { margin: 0; padding: 0; box-sizing: border-box; }
  html, body { width: 1200px; height: 647px; overflow: hidden; background: var(--white); }
  .canvas { position: relative; width: 1200px; height: 647px; background: var(--white); font-family: "Montserrat", sans-serif; }

  .proof-label {
    position: absolute; left: 746px; top: 68px;
    font-family: "Montserrat", sans-serif; font-weight: 500; font-size: 34px;
    letter-spacing: 2px; color: var(--proof-pink);
  }
  .guide { position: absolute; background: var(--guide); }
  .guide-h { height: 0.6px; left: 6px; width: 1188px; }
  .guide-v { width: 0.6px; }

  .billboard { position: absolute; left: 30px; top: 145px; width: 1140px; height: 365px; }
  .billboard-shapes { position: absolute; inset: 0; }

  .headshot {
    position: absolute; left: 88px; top: 33px; width: 190px; height: 333px;
    border-radius: 90px 90px 10px 10px;
    background: linear-gradient(180deg, #d8c49e 0%, #c9a88a 30%, #3f5a3d 60%, #2f4a30 100%);
  }

  .headline-lead {
    position: absolute; left: 300px; width: 490px; top: 27px; text-align: center;
    font-size: 30px; font-weight: 400; letter-spacing: 3px; line-height: 1.2; color: var(--deep-green);
  }
  .headline-main {
    position: absolute; left: 300px; width: 490px; top: 38px; text-align: center;
    font-family: "Playfair Display", serif; font-weight: 500; font-size: 120px; line-height: 1;
    letter-spacing: 4px;
    background: linear-gradient(180deg, var(--gold-dark) 0%, var(--gold-light) 45%, var(--gold-dark) 100%);
    -webkit-background-clip: text; background-clip: text; color: transparent;
  }
  .headline-script {
    position: absolute; left: 420px; width: 250px; top: 150px; text-align: center;
    font-family: "Great Vibes", cursive; font-size: 50px; line-height: 1.1; color: var(--ink);
    white-space: nowrap;
  }
  .script-rule { position: absolute; top: 182px; width: 68px; height: 2px; background: var(--gold); border-radius: 2px; }
  .script-rule-left { left: 349px; }
  .script-rule-right { left: 673px; }

  .services {
    position: absolute; left: 313px; top: 208px; width: 463px; height: 19px;
    background: var(--night); border-radius: 10px;
    display: flex; align-items: center; justify-content: center; gap: 11px;
    font-family: "Poppins", sans-serif; font-weight: 500; font-size: 12.5px; letter-spacing: 0.6px; color: var(--white);
  }
  .services .dot { width: 5px; height: 5px; border-radius: 50%; background: var(--gold); }

  .brand-card {
    position: absolute; left: 444px; top: 236px; width: 196px; height: 96px;
    background: var(--white); border: 3px solid var(--deep-green); border-radius: 12px;
    display: flex; align-items: center; justify-content: center; text-align: center;
  }
  .brand-name {
    font-family: "Poppins", sans-serif; font-weight: 600; font-size: 25px; line-height: 1.1; color: var(--deep-green);
  }

  .scan-photo {
    position: absolute; left: 819px; top: 39px; width: 204px; height: 222px;
    border: 4px solid var(--gold); border-radius: 20px;
    background: linear-gradient(90deg, #b87d6f 0%, #8a4c44 45%, #1a0c0a 50%, #8a4c44 55%, #b87d6f 100%);
  }

  .contact-icon { position: absolute; left: 672px; top: 276px; width: 56px; height: 56px; }
  .phone-number {
    position: absolute; left: 745px; top: 268px; width: 281px;
    font-family: "Poppins", sans-serif; font-weight: 600; font-size: 41px; letter-spacing: 0.5px; color: var(--cream);
    white-space: nowrap;
  }
  .location {
    position: absolute; left: 750px; top: 316px; width: 276px;
    display: flex; align-items: center; gap: 10px;
    font-size: 15px; letter-spacing: 0.8px; color: var(--gold); white-space: nowrap;
  }
  .location .rule { flex: 1; height: 1px; background: var(--gold); }
</style>
</head>
<body>
<div class="canvas">
  <div class="proof-label">REVISED (10.6” X 36”)</div>

  <section class="billboard">
    <svg class="billboard-shapes" width="1140" height="365" viewBox="0 0 1140 365" aria-hidden="true">
      <defs>
        <linearGradient id="dark-field" x1="0" y1="0" x2="1" y2="0">
          <stop offset="0" stop-color="#2a3a30"/>
          <stop offset="0.3" stop-color="#27332b"/>
          <stop offset="0.6" stop-color="#1c221e"/>
          <stop offset="1" stop-color="#1b211d"/>
        </linearGradient>
        <linearGradient id="gold-edge" x1="0" y1="0" x2="1" y2="1">
          <stop offset="0" stop-color="#a8722c"/>
          <stop offset="0.5" stop-color="#ecc46c"/>
          <stop offset="1" stop-color="#c8963e"/>
        </linearGradient>
      </defs>
      <rect class="cream-field" x="0" y="11" width="1133" height="354" fill="#f7f3ee"/>
      <path class="dark-field" d="M0 0 H232 C295 45 312 170 282 235 C275 255 268 275 268 292 Q560 238 786 250 T1140 273 V365 H0 Z" fill="url(#dark-field)"/>
      <path class="gold-edge" d="M232 0 C295 45 312 170 282 235 C275 255 268 275 268 292 Q560 238 786 250 T1140 273" fill="none" stroke="url(#gold-edge)" stroke-width="4"/>
    </svg>

    <div class="headshot" role="img" aria-label="Portrait of the studio owner in green scrubs holding an ultrasound probe"></div>

    <div class="headline-lead">MEET YOUR</div>
    <div class="headline-main">BABY</div>
    <span class="script-rule script-rule-left"></span>
    <div class="headline-script">Before Birth</div>
    <span class="script-rule script-rule-right"></span>

    <div class="services">
      <span>4D ULTRASOUND</span><span class="dot"></span>
      <span>EARLY GENDER</span><span class="dot"></span>
      <span>PREGNANCY CONFIRMATION</span>
    </div>

    <div class="brand-card">
      <div class="brand-name">4D Cradle<br>Glimpse</div>
    </div>

    <div class="scan-photo" role="img" aria-label="4D ultrasound image of twin babies facing each other"></div>

    <svg class="contact-icon" viewBox="0 0 56 56" aria-hidden="true">
      <circle cx="28" cy="28" r="26" fill="none" stroke="#c8963e" stroke-width="2"/>
      <path d="M20 16 c2-1 4-1 5 1 l2 5 c1 2 0 3-1 4 l-2 1 c1 4 4 8 8 10 l2-2 c1-1 2-1 4 0 l4 3 c1 1 1 3 0 4 l-2 2 c-3 2-8 1-13-4 c-6-6-10-14-8-20 z" fill="#c8963e"/>
    </svg>
    <div class="phone-number">850-471-5923</div>
    <div class="location"><span class="rule"></span><span>ELMWAY, FLORIDA</span><span class="rule"></span></div>
  </section>

  <span class="guide guide-h" style="top:166px"></span>
  <span class="guide guide-h" style="top:491px"></span>
  <span class="guide guide-v" style="left:49px; top:112px; height:422px"></span>
  <span class="guide guide-v" style="left:1151px; top:96px; height:454px"></span>
</div>
</body>
</html>
```